Tranquil Harbour Hypnotherapy 2017 DL Card Flyer

We would like a double sided DL Card Flyer design.

We are a professional Hypnotherapy Clinic looking for a fresh clean design.

Front of card is summary info and back of flyer is detailed text.

I have attached documents with text for the front (dl size hypno 1) and back (dl size hypno 2) of the card and an indicative style of layout.

There are logo files uploaded as well as one image file.

The colors we like are blue, white and yellow/gold.
Updates

please note: when using the 'new mindset new results' image, please only use the top half of the image. The girl is not to be in the image, just the words and light bulb with the chalk underline. thanks.. Added Sunday, March 19, 2017

Industry/Entity Type

Health And Wellness

Requirements
Must have
• Note. I have misspelled the www.TranquilHarbourHypnotherapy.com.au (missing an 'o' in the attachments to the brief). My error. Please amend in your design submissions.

```html
<!DOCTYPE html>
<html lang="en">
<head>
<meta charset="utf-8">
<title>Tranquil Harbour Hypnotherapy – DL Flyer</title>
<link href="https://fonts.googleapis.com/css2?family=Roboto+Condensed:wght@400;700&family=Open+Sans:wght@400&display=swap" rel="stylesheet">
<style>
  :root{
    --navy:#262e6b;
    --navy-deep:#1f2660;
    --grey:#a7a9ac;
    --pink:#f4cdd3;
    --sky-top:#7fb8e6;
    --sky-mid:#cfe6f5;
    --sea:#3aa3c4;
    --ink:#222;
    --white:#fff;
    --stage:#3b3b3d;
  }
  *{box-sizing:border-box;margin:0;padding:0}
  html,body{width:1200px;height:1200px;overflow:hidden;background:var(--stage)}
  body{position:relative;font-family:"Roboto Condensed",sans-serif}
  .card{position:absolute;top:127px;width:446px;height:946px;overflow:hidden;background:var(--white);box-shadow:0 6px 18px rgba(0,0,0,.45)}
  .card--front{left:100px}
  .card--back{left:654px}
  .card__bg{position:absolute;inset:0}
  .abs{position:absolute}

  /* front */
  .brand{left:118px;top:46px;display:flex;align-items:center;gap:14px}
  .brand__dot{width:58px;height:58px;border-radius:50%;background:var(--navy)}
  .brand__name{color:var(--navy);font-weight:700;font-size:21px;line-height:1.05;letter-spacing:.5px}
  .quote{left:0;width:446px;top:316px;text-align:center;color:var(--white);text-transform:uppercase}
  .quote__lead{font-size:25px;line-height:32px}
  .quote__big{font-family:"Open Sans",sans-serif;font-size:44px;line-height:48px;letter-spacing:1px}
  .programs{left:0;width:446px;top:468px;text-align:center;color:var(--navy);font-weight:700;font-size:25px;line-height:32px}
  .svc{color:var(--navy);font-weight:700;font-size:22px;line-height:26px;text-transform:uppercase}
  .svc small{display:block;font-weight:400;font-size:11px;line-height:12px}
  .footer-call{left:0;width:446px;top:878px;text-align:center;color:var(--white);font-weight:700;font-size:24px}
  .footer-url{left:0;width:446px;top:910px;text-align:center;color:var(--white);font-size:15px}

  /* back */
  .bulb{left:22px;top:46px;width:124px;height:156px;border-radius:50% 50% 30% 30%;background:radial-gradient(circle at 50% 40%,#5a63a0,var(--navy) 70%)}
  .headline{left:150px;width:290px;top:58px;text-align:center;color:var(--white);text-transform:uppercase}
  .headline__row{font-size:33px;line-height:36px}
  .headline__row small{font-size:21px}
  .headline__call{font-weight:700;font-size:22px;line-height:28px}
  .headline__url{font-size:14.5px;line-height:18px;text-transform:none}
  .detail{left:31px;width:396px;color:var(--ink)}
  .detail__title{color:var(--navy);font-size:22px;line-height:21px;text-transform:uppercase}
  .detail__title small{font-size:11px}
  .detail__body{font-size:11.6px;line-height:15.3px;margin-top:4px}
  .detail__body--sans{font-family:"Open Sans",sans-serif;font-size:11.2px}
  .detail__body b{color:var(--navy);font-family:"Roboto Condensed",sans-serif;font-weight:700;font-size:13px}
  .note{left:0;width:446px;top:884px;text-align:center;color:var(--white);font-size:13.5px;line-height:17px;text-transform:uppercase}
</style>
</head>
<body>

<!-- FRONT -->
<section class="card card--front">
  <svg class="card__bg" width="446" height="946" viewBox="0 0 446 946">
    <defs>
      <linearGradient id="sky" x1="0" y1="0" x2="0" y2="1">
        <stop offset="0" stop-color="var(--sky-top)"/>
        <stop offset=".45" stop-color="var(--sky-mid)"/>
        <stop offset=".75" stop-color="var(--sea)"/>
        <stop offset="1" stop-color="#d9b79a"/>
      </linearGradient>
      <linearGradient id="pale" x1="0" y1="0" x2="0" y2="1">
        <stop offset="0" stop-color="#ffffff"/>
        <stop offset=".5" stop-color="#dcecf8"/>
        <stop offset="1" stop-color="#ffffff"/>
      </linearGradient>
    </defs>
    <rect width="446" height="320" fill="url(#sky)" role="img" aria-label="Photo of a happy family on a sunny beach with arms outstretched"/>
    <rect y="440" width="446" height="430" fill="url(#pale)"/>
    <path d="M190 292 C300 282 390 268 446 244 L446 262 C330 282 250 292 190 292Z" fill="var(--grey)"/>
    <path d="M0 300 C150 294 330 284 446 262 L446 432 C300 440 130 452 0 476Z" fill="var(--navy)"/>
    <path d="M0 476 C130 452 300 440 446 432 L446 448 C300 452 130 470 0 500Z" fill="var(--grey)"/>
    <!-- icons -->
    <g fill="none" stroke="#222" stroke-width="2.5">
      <circle cx="78" cy="580" r="30" fill="var(--pink)" stroke="none"/>
      <rect x="40" y="544" width="62" height="64" rx="10"/>
      <rect x="48" y="552" width="46" height="46" rx="6"/>
      <path d="M64 560 h14 v10 h-14z"/><line x1="71" y1="562" x2="71" y2="567"/>
      <circle cx="362" cy="568" r="30" fill="var(--pink)" stroke="none"/>
      <rect x="334" y="542" width="30" height="10" rx="2"/>
      <rect x="329" y="552" width="40" height="54" rx="6"/>
      <path d="M352 560 l-10 18 h10 l-6 18 l14 -22 h-10 l6 -14z"/>
      <circle cx="200" cy="650" r="34" fill="var(--pink)" stroke="none"/>
      <circle cx="190" cy="650" r="36"/><circle cx="190" cy="650" r="30"/>
      <line x1="166" y1="626" x2="214" y2="674"/>
      <rect x="164" y="648" width="40" height="9"/>
      <circle cx="362" cy="736" r="32" fill="var(--pink)" stroke="none"/>
      <path d="M352 694 a30 28 0 1 1 14 52 l4 14 -16 -12 a30 28 0 0 1 -2 -54z"/>
      <circle cx="342" cy="716" r="2" fill="#222"/><circle cx="360" cy="716" r="2" fill="#222"/>
      <path d="M338 726 q13 12 26 0"/>
      <circle cx="98" cy="822" r="32" fill="var(--pink)" stroke="none"/>
      <path d="M85 852 L52 818 a20 20 0 0 1 33 -26 a20 20 0 0 1 33 26z"/>
      <path d="M38 818 h30 l8 -12 l10 26 l8 -14 h36"/>
    </g>
    <g stroke="var(--navy)" stroke-width="2.5" fill="var(--navy)">
      <line x1="102" y1="597" x2="274" y2="597"/><circle cx="274" cy="597" r="4"/>
      <line x1="0" y1="683" x2="144" y2="683"/><circle cx="144" cy="683" r="4"/>
      <line x1="286" y1="669" x2="446" y2="669"/><circle cx="286" cy="669" r="4"/>
      <line x1="70" y1="761" x2="338" y2="761"/><circle cx="70" cy="761" r="4"/>
      <line x1="118" y1="847" x2="369" y2="847"/><circle cx="369" cy="847" r="4"/>
    </g>
    <rect y="858" width="446" height="8" fill="var(--grey)"/>
    <rect y="869" width="446" height="77" fill="var(--navy)"/>
    <g stroke="#c9cbe0" stroke-width="1.2" fill="#c9cbe0">
      <line x1="0" y1="916" x2="72" y2="916"/><circle cx="72" cy="916" r="3"/>
      <line x1="365" y1="916" x2="446" y2="916"/><circle cx="365" cy="916" r="3"/>
    </g>
  </svg>

  <div class="abs brand"><span class="brand__dot"></span><span class="brand__name">TRANQUIL HARBOUR<br>HYPNOTHERAPY</span></div>

  <div class="abs quote">
    <p class="quote__lead">“There is nothing more<br>important than</p>
    <p class="quote__big">Good Health”</p>
  </div>

  <h2 class="abs programs">PROFESSIONAL HYPNOSIS<br>THERAPY PROGRAMS</h2>

  <p class="abs svc" style="left:120px;top:546px">Weight Loss<small>&nbsp;&nbsp;(Virtual Gastric Band)</small></p>
  <p class="abs svc" style="left:40px;top:624px;text-align:right;width:104px">Quit<br>Smoking</p>
  <p class="abs svc" style="left:298px;top:614px;text-align:center;width:134px">Sugar<br>Addiction</p>
  <p class="abs svc" style="left:78px;top:702px">Chronic Fatigue &amp;<br>Chronic Pain Relief</p>
  <p class="abs svc" style="left:148px;top:788px">Stress Relief &amp;<br>Deep Relaxation</p>

  <p class="abs footer-call">CALL US NOW 1300 555 014</p>
  <p class="abs footer-url">www.TranquilHarbourHypnotherapy.com.au</p>
</section>

<!-- BACK -->
<section class="card card--back">
  <svg class="card__bg" width="446" height="946" viewBox="0 0 446 946">
    <path d="M150 40 C260 30 380 18 446 0 L446 16 C330 30 240 38 150 40Z" fill="var(--grey)"/>
    <path d="M0 38 C150 50 300 34 446 14 L446 182 C300 185 150 195 0 206Z" fill="var(--navy)"/>
    <path d="M0 206 C150 195 300 185 446 182 L446 196 C300 196 150 205 0 224Z" fill="var(--grey)"/>
    <g fill="none" stroke="#ccc" stroke-width="2">
      <circle cx="362" cy="262" r="30" fill="#fbeef0" stroke="none"/>
      <rect x="328" y="234" width="62" height="62" rx="10"/>
      <circle cx="368" cy="378" r="28" fill="#fbeef0" stroke="none"/>
      <rect x="346" y="360" width="40" height="50" rx="6"/>
      <circle cx="366" cy="492" r="30" fill="#fbeef0" stroke="none"/>
      <circle cx="358" cy="492" r="34"/><line x1="336" y1="468" x2="382" y2="516"/>
      <circle cx="370" cy="602" r="30" fill="#fbeef0" stroke="none"/>
      <circle cx="360" cy="596" r="29"/><path d="M346 604 q14 12 28 0"/>
      <circle cx="366" cy="778" r="28" fill="#fbeef0" stroke="none"/>
      <path d="M356 818 L324 786 a19 19 0 0 1 32 -24 a19 19 0 0 1 32 24z"/>
    </g>
    <g stroke="var(--grey)" stroke-width="1.5" fill="var(--grey)">
      <line x1="0" y1="330" x2="138" y2="330"/><circle cx="138" cy="330" r="3.5"/>
      <line x1="0" y1="452" x2="138" y2="452"/><circle cx="138" cy="452" r="3.5"/>
      <line x1="0" y1="559" x2="138" y2="559"/><circle cx="138" cy="559" r="3.5"/>
      <line x1="0" y1="737" x2="138" y2="737"/><circle cx="138" cy="737" r="3.5"/>
    </g>
    <rect y="860" width="446" height="7" fill="var(--grey)"/>
    <rect y="867" width="446" height="79" fill="var(--navy)"/>
  </svg>

  <div class="abs bulb" role="img" aria-label="Hand-lettered light bulb illustration filled with words about ideas and creativity"></div>

  <div class="abs headline">
    <p class="headline__row">New <small>Mindset</small></p>
    <p class="headline__row"><small>New</small> Results</p>
    <p class="headline__call">Call us now 1300 555 014</p>
    <p class="headline__url">www.TranquilHarbourHypnotherapy.com.au</p>
  </div>

  <article class="abs detail" style="top:232px">
    <h3 class="detail__title">Weight Loss <small>(Virtual Gastric Band)</small></h3>
    <p class="detail__body">Achieve long term weight loss without dieting. Whether it’s losing 3kg or 30kg, we’ll help you become the shape and size you want to be.<br>Our Internationally Accredited Program is proven to be 95% effective in clinical trials. &nbsp;<b>Number of Sessions: 6+</b></p>
  </article>

  <article class="abs detail" style="top:340px">
    <h3 class="detail__title">Sugar Addiction</h3>
    <p class="detail__body">Excess sugar intake can lead to obesity, Type 2 Diabetes and tooth decay. The habit of reaching for soft drinks, chocolate, sweets, cakes and biscuits can be hard to break.<br>By rewiring your subconscious habits, our Program puts you back in control.<br><b>Number of Sessions: 3+</b></p>
  </article>

  <article class="abs detail" style="top:464px">
    <h3 class="detail__title">Quit Smoking</h3>
    <p class="detail__body detail__body--sans">The facts speak for themselves. You are 10 times more likely to quit smoking for good using hypnotherapy.<br>Expect to be a non smoker after completing the first session of our Program. (12 Month Guarantee) &nbsp;<b>Number of Sessions: 2</b></p>
  </article>

  <article class="abs detail" style="top:573px">
    <h3 class="detail__title">Chronic Fatigue &amp;<br>Chronic Pain Relief</h3>
    <p class="detail__body detail__body--sans" style="margin-top:9px">Chronic Fatigue, Fibromyalgia and Chronic Musculoskeletal Pain are diseases of modern living. The symptoms of fatigue and pain are very real, however the cause is usually emotional, and is generally hidden beyond our conscious awareness.<br>Our Program comprises Education and Hypnosis to help you regain your health, your self esteem, your friends and your life, all in a manageable timeframe. &nbsp;<b>Number of Sessions: 2</b></p>
  </article>

  <article class="abs detail" style="top:747px">
    <h3 class="detail__title">Stress Relief &amp;<br>Deep Relaxation</h3>
    <p class="detail__body detail__body--sans">Our Program gently uncovers the true source of your stress, and helps you reconnect to a natural inner calm. We teach you self hypnosis so that you have the tools to continue your experience.<br><b>Number of Sessions: 3+</b></p>
  </article>

  <p class="abs note">All programs include take home CD’s personally recorded<br>by our therapists, using advanced hypnotic techniques.</p>
</section>

</body>
</html>
```